Landing Page Design for Adult Dating Age Verification (18+)

The objective of this task is to design a visually appealing pre-landing page for the adult dating site "Quillmera (site: https://quillmera.com/)" with an age verification mechanism. The pre-landing page will feature two buttons that redirect visitors to the main offer. The design should also include a footer block that includes links to the terms of use, privacy policy, and contact us pages.

Design Requirements:
Develop an age verification section prominently displayed on the pre-landing page.
Design the section to include two buttons labeled "Yes" and "No" for visitors to confirm their age.
Ensure the section is visually appealing and clearly communicates the purpose of age verification.

Visual Appeal:
Create a visually appealing design that aligns with the branding and theme of the "Quillmera" adult dating site.
Use suitable color schemes, typography, and graphics to enhance the overall visual appeal of the pre-landing page.

Layout and Navigation:
Design an engaging and intuitive layout that encourages visitors to interact with the page and proceed to the main offer.
Ensure clear and visible navigation elements that direct visitors to the main offer or provide additional information.

Responsive Design:
Develop a responsive design that provides a seamless user experience across various devices, including desktop and mobile.
Ensure the design elements and layout adapt well to different screen sizes and resolutions.

File Formats and Assets:
Deliver the final design in PSD, AI, or Sketch format, ensuring that the files are well-organized and layered.
Include any necessary images or assets used in the design, ensuring they are of high quality and optimized for web use.

```html
<!DOCTYPE html>
<html lang="en">
<head>
<meta charset="utf-8">
<title>Quillmera – Find Your Match</title>
<link rel="stylesheet" href="https://fonts.googleapis.com/css2?family=Outfit:wght@400;500&display=swap">
<style>
  :root {
    --page-bg: #f1edea;
    --band: #d4b6da;
    --ring: #f1edea;
    --ink: #26242c;
    --muted: #6b6570;
    --accent: #d1105a;
    --accent-ink: #ffffff;
    --mark: #d7bde0;
    --photo-a: #e9e3e0;
    --photo-b: #b59c92;
  }
  * { box-sizing: border-box; margin: 0; padding: 0; }
  html, body { width: 1200px; height: 598px; overflow: hidden; }
  body {
    position: relative;
    background: var(--page-bg);
    font-family: "Outfit", sans-serif;
    color: var(--ink);
  }
  a { color: inherit; text-decoration: none; }
  .side-band {
    position: absolute;
    left: 865px; top: 0;
    width: 335px; height: 598px;
    background: var(--band);
  }
  .hero-ring {
    position: absolute;
    left: 539px; top: 5px;
    width: 600px; height: 600px;
    border-radius: 50%;
    background: var(--ring);
  }
  .hero-photo {
    position: absolute;
    left: 553px; top: 19px;
    width: 572px; height: 572px;
    border-radius: 50%;
    background: radial-gradient(circle at 60% 45%, var(--photo-b) 0%, #d3c3bb 35%, var(--photo-a) 75%);
  }
  .brand {
    position: absolute;
    left: 53px; top: 35px;
    display: flex; align-items: center; gap: 12px;
  }
  .brand-dot {
    width: 68px; height: 68px;
    border-radius: 50%;
    background: var(--mark);
  }
  .brand-name {
    font-size: 36px; font-weight: 500;
    color: var(--ink);
  }
  .verify {
    position: absolute;
    left: 54px; top: 180px;
    width: 350px;
  }
  .verify-title {
    font-size: 46px; font-weight: 500;
    line-height: 52px;
    letter-spacing: -0.5px;
    white-space: nowrap;
  }
  .verify-intro {
    margin-top: 13px;
    font-size: 19px; font-weight: 500;
    line-height: 29px;
  }
  .verify-question {
    margin-top: 15px;
    font-size: 22px; font-weight: 500;
    line-height: 30px;
    white-space: nowrap;
  }
  .verify-actions {
    position: absolute;
    left: 54px; top: 396px;
  }
  .btn {
    position: absolute;
    width: 72px; height: 56px;
    background: var(--accent);
    color: var(--accent-ink);
    font-size: 24px; font-weight: 500;
    display: flex; align-items: center; justify-content: center;
  }
  .btn-yes { left: 0; top: 0; }
  .btn-no { left: 86px; top: 4px; }
  .remember {
    position: absolute;
    left: 55px; top: 472px;
    display: flex; align-items: center; gap: 12px;
    font-size: 18px; font-weight: 500;
  }
  .remember-box {
    width: 16px; height: 16px;
    border: 1.5px solid var(--ink);
    background: #fff;
  }
  .site-footer {
    position: absolute;
    left: 55px; top: 560px;
    display: flex; gap: 22px;
    font-size: 13px; font-weight: 400;
    color: var(--muted);
  }
</style>
</head>
<body>
  <div class="side-band"></div>
  <div class="hero-ring"></div>
  <div class="hero-photo" role="img" aria-label="Photo of a woman in lingerie standing by a bright window"></div>

  <a class="brand" href="https://quillmera.com/">
    <span class="brand-dot"></span>
    <span class="brand-name">Quillmera</span>
  </a>

  <section class="verify">
    <h1 class="verify-title">Find Your Match</h1>
    <p class="verify-intro">Welcome to Our Dating Site.The Place Where Your can Find What Your Heart Desires!</p>
    <p class="verify-question">Are You Over 18 years of Age?</p>
  </section>

  <div class="verify-actions">
    <a class="btn btn-yes" href="https://quillmera.com/">Yes</a>
    <a class="btn btn-no" href="#">No</a>
  </div>

  <label class="remember">
    <span class="remember-box"></span>
    Remember Me
  </label>

  <footer class="site-footer">
    <a href="#">Terms of Use</a>
    <a href="#">Privacy Policy</a>
    <a href="#">Contact Us</a>
  </footer>
</body>
</html>
```